Pepper & Palm Business Card FUN & EXCITING

Here is the Information for the Card:
Jaswinder Bains (Ravi)
E: RaviBains@postlark.com
C: (480) 555-0147
www.PepperPalmLV.com

We don't want traditional Indian cliche, We a playful bold and fun business card.

Files: https://files.cloudvessel.net/share/folders/7TqRmXpZ2vKa9LwBn4YcHd3JsEf6UoGi?usp=share_link

https://files.cloudvessel.net/share/folders/4MzXaQ8rTw2YbNcVk6PsLe5GhJdR3FoU?usp=share_link

Target Market(s)

Las Vegas Local Restaurant

Industry/Entity Type

Indian Restaurant

Contact Information for Business Card

Name, Email, Cell Phone, Company Logo

```html
<!DOCTYPE html>
<html lang="en">
<head>
<meta charset="utf-8">
<title>Pepper &amp; Palm — Business Card</title>
<link href="https://fonts.googleapis.com/css2?family=Zilla+Slab:wght@700&family=Arvo:wght@400;700&family=Nunito+Sans:wght@700&family=Oswald:wght@300&display=swap" rel="stylesheet">
<style>
  :root {
    --backdrop: #969696;
    --card: #ffffff;
    --pink: #d4345c;
    --yellow: #f0c03a;
    --teal: #48a98a;
    --ink: #1c1c1c;
    --art-warm: #f08a3c;
    --art-cream: #f6efc8;
  }
  * { margin: 0; padding: 0; box-sizing: border-box; }
  html, body {
    width: 1200px; height: 1200px; overflow: hidden;
    background: var(--backdrop);
  }
  .card {
    position: absolute;
    left: 226px;
    width: 746px;
    height: 436px;
    background: var(--card);
    overflow: hidden;
  }
  .card--front { top: 91px; }
  .card--back { top: 601px; }

  .holder-name {
    position: absolute; left: 40px; top: 56px;
    font-family: "Zilla Slab", serif; font-weight: 700;
    font-size: 42px; line-height: 1; letter-spacing: 0.3px;
    color: var(--card);
    -webkit-text-stroke: 2px var(--pink);
    paint-order: stroke fill;
    text-shadow: -4px 5px 0 var(--yellow), -7px 9px 0 var(--pink);
    white-space: nowrap;
  }
  .holder-email {
    position: absolute; left: 50px; top: 140px;
    font-family: "Arvo", serif; font-size: 25px;
    color: var(--pink);
  }
  .holder-phone {
    position: absolute; left: 68px; top: 290px;
    font-family: "Nunito Sans", sans-serif; font-weight: 700; font-size: 28px;
    color: var(--teal);
  }
  .holder-site {
    position: absolute; left: 70px; top: 325px;
    font-family: "Arvo", serif; font-size: 26px;
    color: var(--teal);
  }
  .mascot-art {
    position: absolute; left: 361px; top: 134px;
    width: 375px; height: 250px;
  }
  .mascot-tagline {
    position: absolute; left: 449px; top: 390px; width: 200px;
    text-align: center;
    font-family: "Oswald", sans-serif; font-weight: 300; font-size: 16px;
    letter-spacing: 1px; color: var(--ink);
    white-space: nowrap;
  }

  .brand-name {
    position: absolute;
    font-family: "Zilla Slab", serif; font-weight: 700;
    font-size: 88px; line-height: 0.95;
    color: var(--pink);
    text-transform: uppercase;
    white-space: nowrap;
  }
  .brand-name--main { left: 450px; top: 26px; }
  .brand-name--wrap { right: 580px; top: 140px; text-align: right; }
</style>
</head>
<body>
  <section class="card card--front">
    <div class="holder-name">Jaswinder Bains (Ravi)</div>
    <div class="holder-email">ravibains@postlark.com</div>
    <div class="holder-phone">(480) 555-0147</div>
    <div class="holder-site">pepperpalmlv.com</div>
    <svg class="mascot-art" role="img" aria-label="Cartoon illustration of a walking curry bowl and flatbread with hearts and sparkles" viewBox="0 0 375 250">
      <defs>
        <linearGradient id="mascotTone" x1="0" y1="0" x2="1" y2="1">
          <stop offset="0" stop-color="var(--art-warm)" stop-opacity="0.55"/>
          <stop offset="1" stop-color="var(--art-cream)"/>
        </linearGradient>
      </defs>
      <rect width="375" height="250" rx="18" fill="url(#mascotTone)"/>
    </svg>
    <div class="mascot-tagline">“A match made in heaven”</div>
  </section>

  <section class="card card--back">
    <div class="brand-name brand-name--main">Pepper<br>&amp; Palm</div>
    <div class="brand-name brand-name--wrap">Pepper<br>&amp; Palm</div>
  </section>
</body>
</html>
```